New Business Card Design Project

I'd like a business card design around the same modern style that I used on my website www.brovanhs.com
It's gonna be one of those round corners double-sided business cards with maybe a big logo on the front and all the info on the back of the card.

Contact Information for Business Card

Marco Delgado
425-317-6084
www.brovanhs.com

www.facebook.com/BrovanHomeServices
www.intsgram.com/BrovanHomeServices

Requirements
Must have
• it needs to look elegant and modern

```html
<!DOCTYPE html>
<html lang="en">
<head>
<meta charset="utf-8">
<title>Brovan Home Services — Business Card</title>
<link rel="stylesheet" href="https://fonts.googleapis.com/css2?family=Montserrat:wght@500;600;700&display=swap">
<style>
  :root {
    --backdrop: #1a1a1a;
    --card: #262626;
    --card-edge: #2e2e2e;
    --accent: #1b8fd8;
    --text: #f2f2f2;
  }
  * { box-sizing: border-box; margin: 0; padding: 0; }
  html, body { width: 1200px; height: 900px; overflow: hidden; }
  body {
    background: var(--backdrop);
    font-family: "Montserrat", Arial, sans-serif;
    color: var(--text);
    position: relative;
  }
  .card {
    position: absolute;
    left: 280px;
    width: 640px;
    height: 366px;
    background: var(--card);
    border: 1px solid var(--card-edge);
    border-radius: 14px;
  }
  .card--front { top: 44px; display: flex; align-items: center; justify-content: center; }
  .card--back { top: 450px; }

  .brand-name {
    font-size: 40px;
    font-weight: 700;
    color: var(--accent);
    letter-spacing: 0.5px;
    display: flex;
    align-items: center;
    gap: 16px;
  }
  .brand-dot {
    width: 22px; height: 22px;
    border-radius: 50%;
    background: var(--accent);
  }

  .identity {
    position: absolute;
    right: 360px;
    top: 120px;
    text-align: right;
  }
  .identity__name {
    font-size: 30px;
    font-weight: 500;
    color: var(--accent);
    letter-spacing: 1.5px;
    text-transform: uppercase;
    line-height: 1.1;
  }
  .identity__role { font-size: 19px; font-weight: 500; margin-top: 6px; }
  .identity__address { font-size: 17px; font-weight: 500; line-height: 1.45; margin-top: 8px; }

  .divider {
    position: absolute;
    left: 298px;
    top: 118px;
    width: 2px;
    height: 116px;
    background: var(--accent);
  }

  .contact-list {
    position: absolute;
    left: 322px;
    top: 124px;
    list-style: none;
  }
  .contact-list li {
    display: flex;
    align-items: center;
    gap: 10px;
    font-size: 17px;
    font-weight: 500;
    line-height: 1.5;
  }
  .contact-list svg { width: 14px; height: 14px; flex: none; }
  .plain-mark {
    width: 11px; height: 11px; margin: 0 1.5px;
    border-radius: 50%;
    background: var(--accent);
    flex: none;
  }
</style>
</head>
<body>
  <section class="card card--front">
    <div class="brand-name"><span class="brand-dot"></span>Brovan Home Services</div>
  </section>

  <section class="card card--back">
    <div class="identity">
      <p class="identity__name">Marco Delgado</p>
      <p class="identity__role">Director</p>
      <p class="identity__address">2419 Harlow Creek Drive<br>Oklahoma City, OK 73012</p>
    </div>

    <div class="divider"></div>

    <ul class="contact-list">
      <li>
        <svg viewBox="0 0 16 16" aria-hidden="true"><path d="M4 1.5l2.2 3-1.4 1.6c.9 2 2.4 3.5 4.4 4.4l1.6-1.4 3 2.2-1.4 2.6C7 13.8 2.2 9 1.4 2.9z" fill="none" stroke="var(--accent)" stroke-width="1.4" stroke-linejoin="round"/></svg>
        425-317-6084
      </li>
      <li>
        <svg viewBox="0 0 16 16" aria-hidden="true"><rect x="1.5" y="3.5" width="13" height="9" rx="1" fill="none" stroke="var(--accent)" stroke-width="1.4"/><path d="M2 4l6 5 6-5" fill="none" stroke="var(--accent)" stroke-width="1.4"/></svg>
        info@brovanhs.com
      </li>
      <li>
        <svg viewBox="0 0 16 16" aria-hidden="true"><circle cx="8" cy="8" r="6.3" fill="none" stroke="var(--accent)" stroke-width="1.3"/><ellipse cx="8" cy="8" rx="2.8" ry="6.3" fill="none" stroke="var(--accent)" stroke-width="1.1"/><path d="M1.8 8h12.4" stroke="var(--accent)" stroke-width="1.1"/></svg>
        www.brovanhs.com
      </li>
      <li><span class="plain-mark"></span>/BrovanHomeServices</li>
      <li><span class="plain-mark"></span>/BrovanHomeServices</li>
    </ul>
  </section>
</body>
</html>
```